Business Card Design Project

I need a business card designed from scratch. I have an existing logo that I can upload in Illustrator for modification or redesign.

The Company is called Query Lanterns http://querylanterns.com.au and we provide Search Engine Optimization services to Australian businesses. The current logo signifies an increase in visitors, profits etc...

There are no restrictions as to the redesign - colours, style etc are all open to change.

Cards will be full colour and one sided printed at http://www.cardmoxel.com.au so check their requirements for file format and sizes etc.

I will expect all original files upon completion of project.

Target Market(s)

Any business with a web site looking to improve their search engine rankings

Industry/Entity Type

Business

Requirements
Must have
• I like modern, sleek designs. Clean, not fussy, uncluttered.

```html
<!DOCTYPE html>
<html lang="en">
<head>
<meta charset="utf-8">
<title>Query Lanterns – Business Cards</title>
<link href="https://fonts.googleapis.com/css2?family=Source+Sans+3:wght@400;600;700&display=swap" rel="stylesheet">
<style>
  :root {
    --backdrop: #b0841f;
    --card: #ffffff;
    --brand-blue: #1a73b8;
    --brand-navy: #1e3f66;
    --blue-light: #3a8bc8;
    --gold: #f5b51b;
    --gold-light: #efdc52;
    --ink: #222222;
  }
  * { margin: 0; padding: 0; box-sizing: border-box; }
  html, body { width: 1200px; height: 686px; overflow: hidden; }
  body {
    background: var(--backdrop);
    font-family: "Source Sans 3", "Helvetica Neue", Arial, sans-serif;
    position: relative;
  }
  .card {
    position: absolute;
    width: 451px;
    height: 257px;
    background: var(--card);
    border-radius: 26px;
    overflow: hidden;
    box-shadow: 2px 3px 4px rgba(0,0,0,0.45);
  }
  .card--front { left: 110px; top: 80px; }
  .card--back-wave { left: 616px; top: 80px; }
  .card--back-plain { left: 369px; top: 374px; }

  .brand {
    position: absolute;
    left: 0; right: 0;
    display: flex;
    align-items: center;
    justify-content: center;
    gap: 10px;
    color: var(--brand-blue);
    font-weight: 700;
    letter-spacing: -0.3px;
  }
  .brand__dot {
    border-radius: 50%;
    background: var(--gold);
    flex: none;
  }
  .card--front .brand { top: 40px; font-size: 34px; }
  .card--front .brand__dot { width: 18px; height: 18px; }
  .card--back-wave .brand { top: 78px; font-size: 42px; }
  .card--back-wave .brand__dot { width: 22px; height: 22px; }
  .card--back-plain .brand { top: 103px; font-size: 42px; }
  .card--back-plain .brand__dot { width: 22px; height: 22px; }

  .person {
    position: absolute;
    top: 124px; left: 0; right: 0;
    text-align: center;
    font-size: 0;
  }
  .person__name {
    font-size: 19px;
    font-weight: 700;
    color: var(--brand-blue);
  }
  .person__divider {
    display: inline-block;
    width: 1px; height: 17px;
    background: var(--brand-blue);
    margin: 0 8px;
    vertical-align: -2px;
  }
  .person__title {
    font-size: 14px;
    font-weight: 600;
    color: var(--gold);
  }
  .contact {
    position: absolute;
    top: 151px; left: 0; right: 0;
    display: flex;
    justify-content: center;
    gap: 20px;
    font-size: 13px;
    color: var(--ink);
  }
  .contact__item { display: flex; align-items: center; gap: 4px; }
  .contact__icon { width: 11px; height: 11px; fill: var(--brand-blue); }
  .address {
    position: absolute;
    top: 170px; left: 0; right: 0;
    text-align: center;
    font-size: 13px;
    color: var(--ink);
  }
  .wave { position: absolute; left: 0; top: 0; width: 451px; height: 257px; }
  .website {
    position: absolute;
    right: 26px; top: 228px;
    font-size: 13px;
    font-weight: 700;
    color: #ffffff;
  }
</style>
</head>
<body>

<svg width="0" height="0" style="position:absolute">
  <defs>
    <linearGradient id="band-gold" x1="0" x2="1" y1="0" y2="0">
      <stop offset="0" stop-color="#efdc52"/>
      <stop offset="1" stop-color="#f5b51b"/>
    </linearGradient>
    <linearGradient id="band-blue" x1="0" x2="1" y1="0" y2="0">
      <stop offset="0" stop-color="#3a8bc8"/>
      <stop offset="0.45" stop-color="#2c6aa3"/>
      <stop offset="1" stop-color="#1e3f66"/>
    </linearGradient>
  </defs>
</svg>

<section class="card card--front">
  <svg class="wave" viewBox="0 0 451 257" aria-hidden="true">
    <path d="M0,198 C120,214 200,226 280,216 C350,206 400,190 451,188 L451,257 L0,257 Z" fill="url(#band-gold)"/>
    <path d="M0,214 C110,232 200,236 290,224 C360,214 410,208 451,206 L451,257 L0,257 Z" fill="url(#band-blue)" stroke="#ffffff" stroke-width="2"/>
  </svg>
  <div class="brand"><span class="brand__dot"></span><span class="brand__name">Query Lanterns</span></div>
  <p class="person"><span class="person__name">Your Name</span><span class="person__divider"></span><span class="person__title">Title</span></p>
  <div class="contact">
    <span class="contact__item">
      <svg class="contact__icon" viewBox="0 0 12 12" aria-hidden="true"><path d="M2.5 0.5 L4.5 0.5 L5.3 3.2 L3.9 4.3 C4.6 5.9 6.1 7.4 7.7 8.1 L8.8 6.7 L11.5 7.5 L11.5 9.5 C11.5 10.6 10.6 11.5 9.5 11.5 C4.5 11.5 0.5 7.5 0.5 2.5 C0.5 1.4 1.4 0.5 2.5 0.5 Z"/></svg>
      123-456-7890
    </span>
    <span class="contact__item">
      <svg class="contact__icon" viewBox="0 0 12 12" aria-hidden="true"><path d="M0.5 2.5 H11.5 V10 H0.5 Z" /><path d="M0.8 2.8 L6 6.6 L11.2 2.8" fill="none" stroke="#ffffff" stroke-width="1"/></svg>
      inquiry@querylanterns.com.au
    </span>
  </div>
  <p class="address">Street name City State, zip code</p>
  <p class="website">www.querylanterns.com.au</p>
</section>

<section class="card card--back-wave">
  <svg class="wave" viewBox="0 0 451 257" aria-hidden="true">
    <path d="M0,198 C120,214 200,226 280,216 C350,206 400,190 451,188 L451,257 L0,257 Z" fill="url(#band-gold)"/>
    <path d="M0,214 C110,232 200,236 290,224 C360,214 410,208 451,206 L451,257 L0,257 Z" fill="url(#band-blue)" stroke="#ffffff" stroke-width="2"/>
  </svg>
  <div class="brand"><span class="brand__dot"></span><span class="brand__name">Query Lanterns</span></div>
</section>

<section class="card card--back-plain">
  <div class="brand"><span class="brand__dot"></span><span class="brand__name">Query Lanterns</span></div>
</section>

</body>
</html>
```